Business Card Design Project

Keep it simple , using logo and colors that compliment. Logo on one side with complimentary back ground color. Other side, personal info with possible complimentary design/colors

Target Market(s)

we are a non for profit that will be seeking donations . Both monetary and in kind

Industry/Entity Type

Business

Font styles to use
Sans Serif

Colors

Designer to choose colors to be used in the design.

```html
<!DOCTYPE html>
<html lang="en">
<head>
<meta charset="utf-8">
<title>Open Hand Fund – Business Card</title>
<link rel="stylesheet" href="https://fonts.googleapis.com/css2?family=Lato:wght@400;700;900&family=Montserrat:wght@800&display=swap">
<style>
  :root {
    --navy: #232a4d;
    --yellow: #e6d20c;
    --yellow-soft: #f3e87a;
    --white: #f4f4f4;
    --ink: #1f2340;
    --backdrop: #2b2b2b;
  }
  * { margin: 0; padding: 0; box-sizing: border-box; }
  html, body {
    width: 1200px; height: 997px; overflow: hidden;
    background: var(--backdrop);
  }
  .sheet {
    position: relative; width: 1200px; height: 997px;
    display: flex; flex-direction: column; align-items: center; justify-content: center; gap: 56px;
  }
  .card {
    width: 560px; height: 320px; border-radius: 22px; overflow: hidden;
    box-shadow: 0 18px 40px rgba(0,0,0,.55);
  }
  .card svg { display: block; width: 100%; height: 100%; }
  .org-name { font-family: "Lato", sans-serif; font-weight: 700; fill: var(--yellow); }
  .person-name { font-family: "Montserrat", sans-serif; font-weight: 800; font-size: 25px; fill: var(--yellow); }
  .person-role { font-family: "Lato", sans-serif; font-weight: 700; font-size: 16px; fill: var(--white); }
  .contact { font-family: "Lato", sans-serif; font-weight: 700; font-size: 15px; fill: var(--ink); }
</style>
</head>
<body>
<main class="sheet">

  <!-- Front: organisation name -->
  <section class="card card--front" aria-label="Card front">
    <svg viewBox="0 0 560 320" xmlns="http://www.w3.org/2000/svg">
      <rect class="card-base" width="560" height="320" fill="var(--white)"/>
      <path class="band band--yellow" d="M0,0 H560 V52 C420,82 310,130 230,180 C160,225 80,252 0,262 Z" fill="var(--yellow)"/>
      <path class="band band--pale" d="M0,0 H560 V44 C420,74 310,122 230,172 C160,217 80,244 0,254 Z" fill="var(--yellow-soft)"/>
      <path class="band band--navy" d="M0,0 H560 V34 C420,64 310,112 230,162 C160,207 80,234 0,244 Z" fill="var(--navy)"/>
      <circle class="name-disc" cx="290" cy="140" r="82" fill="var(--navy)" stroke="var(--yellow)" stroke-width="7"/>
      <text class="org-name" x="290" y="122" font-size="24" text-anchor="middle">Open</text>
      <text class="org-name" x="290" y="150" font-size="24" text-anchor="middle">Hand</text>
      <text class="org-name" x="290" y="178" font-size="24" text-anchor="middle">Fund</text>
    </svg>
  </section>

  <!-- Back: personal details -->
  <section class="card card--back" aria-label="Card back">
    <svg viewBox="0 0 560 320" xmlns="http://www.w3.org/2000/svg">
      <rect class="card-base" width="560" height="320" fill="var(--white)"/>
      <path class="band band--yellow" d="M0,0 H560 V96 C440,110 330,140 230,180 C150,212 70,228 0,232 Z" fill="var(--yellow)"/>
      <path class="band band--pale" d="M0,0 H560 V88 C440,102 330,132 230,172 C150,204 70,220 0,224 Z" fill="var(--yellow-soft)"/>
      <path class="band band--navy" d="M0,0 H560 V78 C440,92 330,122 230,162 C150,194 70,210 0,214 Z" fill="var(--navy)"/>

      <circle class="name-disc" cx="462" cy="80" r="62" fill="var(--navy)" stroke="var(--yellow)" stroke-width="6"/>
      <text class="org-name" x="462" y="62" font-size="18" text-anchor="middle">Open</text>
      <text class="org-name" x="462" y="84" font-size="18" text-anchor="middle">Hand</text>
      <text class="org-name" x="462" y="106" font-size="18" text-anchor="middle">Fund</text>

      <text class="person-name" x="40" y="112">Daniel Okafor</text>
      <text class="person-role" x="40" y="136">Owner</text>

      <!-- email -->
      <g class="contact-line">
        <circle cx="300" cy="232" r="10" fill="var(--navy)"/>
        <rect x="294" y="228" width="12" height="8" fill="var(--yellow)"/>
        <path d="M294,228 L300,233 L306,228" stroke="var(--navy)" stroke-width="1.2" fill="none"/>
        <text class="contact" x="318" y="237">lena.hartmann@openhandfund.org</text>
      </g>
      <!-- web -->
      <g class="contact-line">
        <circle cx="300" cy="258" r="10" fill="var(--navy)"/>
        <path d="M296,262 L304,254" stroke="var(--yellow)" stroke-width="2.2" stroke-linecap="round"/>
        <circle cx="296" cy="262" r="2.4" fill="none" stroke="var(--yellow)" stroke-width="1.4"/>
        <circle cx="304" cy="254" r="2.4" fill="none" stroke="var(--yellow)" stroke-width="1.4"/>
        <text class="contact" x="318" y="263">www.openhandfund.org</text>
      </g>
      <!-- phone -->
      <g class="contact-line">
        <circle cx="52" cy="258" r="10" fill="var(--navy)"/>
        <path d="M46,255 Q52,249 58,255 L56,257 L54,255 L50,255 L48,257 Z" fill="var(--yellow)"/>
        <rect x="48" y="258" width="8" height="5" rx="1" fill="var(--yellow)"/>
        <text class="contact" x="70" y="263">0049 170 2284519</text>
      </g>
      <!-- fax -->
      <g class="contact-line">
        <circle cx="52" cy="284" r="10" fill="var(--navy)"/>
        <rect x="49" y="277" width="6" height="4" fill="var(--yellow)"/>
        <rect x="46" y="281" width="12" height="6" rx="1" fill="var(--yellow)"/>
        <rect x="49" y="286" width="6" height="3" fill="var(--yellow)"/>
        <text class="contact" x="70" y="289">0049 170 2284510</text>
      </g>
    </svg>
  </section>

</main>
</body>
</html>
```